Fun, Clean Business Card For Family Focused Travel Agency

I need a business card using specific colors and fonts as in the uploaded files. Ideally, I would like a large image of the logo on the back and all the contact info on the front. Maybe the stars/dots somewhere in a flowy form.

I do want it the contact information to be clear and easy to read. I don't want it to look too busy. Maybe even a bit minimalist.

I plan or ordering the ROUNDED CORNER business cards from Cardwell Press, so please consider that in your design.

Target Market(s)

Families with children, couples, groups of friends

Contact Information for Business Card

Marla Quint, Owner
Marla@TumbleTrips.example
Cell Phone Number 555-218-4603
Office Phone Number 555-647-1925
Specializing in Glimmerland destinations, Pelican Bay Fun Park, Cruises and All-Inclusive Vacations.

Nice but not required:
www.TumbleTrips.example
Facebook, Instagram, Twitter icons with username: TumbleTrips

Font styles to use
Sans Serif

Requirements
Must have
• Please try to use the colors from the logo as much as possible. I understand lighter shades/colors may be needed for some things.
Should not have
• NO SERIF FONTS. That is really the only thing I do not want at all

```html
<!DOCTYPE html>
<html lang="en">
<head>
<meta charset="utf-8">
<title>Tumble Trips – Business Card</title>
<link rel="stylesheet" href="https://fonts.googleapis.com/css2?family=Open+Sans:wght@400;600;700&display=swap">
<style>
  :root {
    --navy: #141a3d;
    --teal: #1cc3ad;
    --paper: #ffffff;
    --backdrop: #e9e7e2;
    --ink-light: #f2f4f8;
  }
  * { margin: 0; padding: 0; box-sizing: border-box; }
  html, body { width: 1200px; height: 780px; overflow: hidden; }
  body {
    background: var(--backdrop);
    font-family: "Open Sans", Arial, sans-serif;
    position: relative;
  }
  .card {
    position: absolute;
    top: 235px;
    width: 540px;
    height: 309px;
    border-radius: 18px;
    overflow: hidden;
    box-shadow: 0 6px 20px rgba(0,0,0,0.18);
  }
  .card--front { left: 40px; background: var(--paper); }
  .card--back { left: 620px; background: var(--navy); }

  .front-wave { position: absolute; inset: 0; }
  .brand {
    position: absolute;
    display: flex;
    align-items: center;
    gap: 10px;
    font-family: "Open Sans", Arial, sans-serif;
    font-weight: 700;
    line-height: 1;
    white-space: nowrap;
  }
  .brand__dot { border-radius: 50%; background: var(--teal); flex: none; }
  .card--front .brand { top: 14px; right: 40px; color: var(--navy); font-size: 24px; }
  .card--front .brand__dot { width: 22px; height: 22px; }

  .holder { position: absolute; left: 30px; top: 106px; }
  .holder__name {
    font-family: "Open Sans", Arial, sans-serif;
    font-weight: 600;
    color: var(--ink-light);
    font-size: 24px;
    line-height: 1.1;
  }
  .holder__role { color: var(--teal); font-size: 12px; margin-left: 30px; margin-top: 2px; }

  .contact-list { position: absolute; left: 30px; top: 163px; list-style: none; }
  .contact-list li {
    display: flex; align-items: center; gap: 8px;
    color: var(--ink-light); font-size: 11.5px; height: 16px;
  }
  .contact-icon { width: 12px; height: 12px; flex: none; }

  .specialty {
    position: absolute; left: 30px; top: 236px;
    color: var(--ink-light); font-size: 11.5px; line-height: 15px;
  }
  .specialty__lead { color: var(--teal); font-weight: 600; }

  .social { position: absolute; left: 30px; top: 275px; display: flex; align-items: center; gap: 5px; }
  .social__tile { width: 16px; height: 16px; border-radius: 2px; background: var(--teal); }
  .social__handle { color: var(--ink-light); font-size: 11.5px; font-weight: 600; margin-left: 6px; }

  .side-tab {
    position: absolute; left: -9px; top: 150px;
    width: 18px; height: 18px; border-radius: 50%; background: var(--teal);
  }

  .card--back .brand { top: 110px; left: 50%; transform: translateX(-50%); color: var(--paper); font-size: 44px; }
  .card--back .brand__dot { width: 40px; height: 40px; }
  .back-url {
    position: absolute; top: 190px; width: 100%; text-align: center;
    color: var(--paper); font-size: 13px; letter-spacing: 4px;
  }
</style>
</head>
<body>
  <section class="card card--front" aria-label="Card front">
    <svg class="front-wave" viewBox="0 0 540 309" width="540" height="309" aria-hidden="true">
      <path d="M0,86 C190,98 360,92 540,60 L540,309 L0,309Z" fill="var(--teal)"/>
      <path d="M0,98 C200,110 370,102 540,72 L540,309 L0,309Z" fill="var(--navy)"/>
    </svg>
    <div class="side-tab"></div>
    <div class="brand"><span class="brand__dot"></span>Tumble Trips</div>

    <div class="holder">
      <div class="holder__name">Marla Quint</div>
      <div class="holder__role">Owner</div>
    </div>

    <ul class="contact-list">
      <li>
        <svg class="contact-icon" viewBox="0 0 12 12"><circle cx="6" cy="6" r="6" fill="var(--teal)"/><rect x="4" y="2.5" width="4" height="7" rx="0.8" fill="none" stroke="var(--navy)" stroke-width="1"/></svg>
        555-218-4603
      </li>
      <li>
        <svg class="contact-icon" viewBox="0 0 12 12"><circle cx="6" cy="6" r="6" fill="var(--teal)"/><path d="M3.5 3.5 C3.5 6.5 5.5 8.5 8.5 8.5 L8.5 7.2 L7.2 6.6 L6.6 7.2 C5.7 6.8 5.2 6.3 4.8 5.4 L5.4 4.8 L4.8 3.5Z" fill="var(--navy)"/></svg>
        555-647-1925
      </li>
      <li>
        <svg class="contact-icon" viewBox="0 0 12 12"><circle cx="6" cy="6" r="6" fill="var(--teal)"/><rect x="3" y="4" width="6" height="4.2" fill="none" stroke="var(--navy)" stroke-width="0.9"/><path d="M3 4 L6 6.4 L9 4" fill="none" stroke="var(--navy)" stroke-width="0.9"/></svg>
        Marla@TumbleTrips.example
      </li>
      <li>
        <svg class="contact-icon" viewBox="0 0 12 12"><circle cx="6" cy="6" r="6" fill="var(--teal)"/><circle cx="6" cy="6" r="3" fill="none" stroke="var(--navy)" stroke-width="0.9"/><path d="M3 6 H9 M6 3 V9" stroke="var(--navy)" stroke-width="0.8"/></svg>
        www.TumbleTrips.example
      </li>
    </ul>

    <p class="specialty">
      <span class="specialty__lead">Specializing in</span> Glimmerland destinations<br>
      Pelican Bay Fun Park | Cruises and All-Inclusive Vacations.
    </p>

    <div class="social">
      <span class="social__tile"></span>
      <span class="social__tile"></span>
      <span class="social__tile"></span>
      <span class="social__handle">TumbleTrips</span>
    </div>
  </section>

  <section class="card card--back" aria-label="Card back">
    <div class="brand"><span class="brand__dot"></span>Tumble Trips</div>
    <div class="back-url">www.TumbleTrips.example</div>
  </section>
</body>
</html>
```